Ferncliff Capital - Website Design

We need a website design for a new commercial real estate company called Ferncliff Capital. We're effectively commercial mortgage brokers connecting real estate investors to lenders. We need a website that is simple (not busy), elegant, professional, and user-friendly. A lot of the users will be in their 50's and less tech savvy, so a stream-lined design is best. The website will serve as a portal for lenders to review new financing opportunities, as well as for real estate investors to review terms from lenders.
Updates
Just uploaded our logo.
Target Market(s)
Commercial real estate investors and lenders
Industry/Entity Type
Real Estate
Number of Pages Required
1 page
Colors
Designer to choose colors to be used in the design.
Look and feel

```html
<!DOCTYPE html>
<html lang="en">
<head>
<meta charset="utf-8">
<title>Ferncliff Capital</title>
<link href="https://fonts.googleapis.com/css2?family=Poppins:ital,wght@0,300;0,400;0,500;0,600;1,400&display=swap" rel="stylesheet">
<style>
:root{
  --brand:#125b8f;
  --brand-dark:#0e4a78;
  --ink:#1d1d1d;
  --muted:#8a8a8a;
  --white:#ffffff;
  --dark-band:#1f1f22;
  --footer:#0d4a8c;
}
*{margin:0;padding:0;box-sizing:border-box}
html,body{width:1200px;height:3629px;overflow:hidden}
body{font-family:"Poppins",sans-serif;color:var(--ink);background:var(--white);position:relative}
section,header,footer{position:absolute;left:0;width:1200px;overflow:hidden}
.abs{position:absolute}

/* Hero */
.hero{top:0;height:569px}
.hero-photo{position:absolute;inset:0;background:linear-gradient(100deg,#5fa7b0 0%,#7db9bf 30%,#9aa7b3 55%,#b06a78 80%,#a94a58 100%)}
.hero-photo::after{content:"";position:absolute;inset:0;background:linear-gradient(180deg,rgba(20,20,30,.45) 0%,rgba(20,20,30,0) 25%)}
.nav{position:absolute;top:0;left:0;width:1200px;height:96px}
.brand{position:absolute;left:84px;top:34px;font-size:24px;font-weight:600;color:var(--white)}
.menu{position:absolute;left:414px;top:40px;display:flex;gap:34px;font-size:13px;color:var(--white);list-style:none}
.social-top{position:absolute;left:963px;top:32px;display:flex;gap:8px}
.social-top span{width:32px;height:32px;border-radius:50%;display:block}
.welcome-panel{position:absolute;left:266px;top:194px;width:678px;height:302px;background:rgba(64,178,190,.55);text-align:center}
.welcome-panel .kicker{margin-top:26px;font-size:40px;font-weight:600;color:var(--ink)}
.welcome-panel .name{font-size:54px;font-weight:300;color:var(--ink);line-height:1.05}
.welcome-panel .tag{font-size:23px;color:#2a2a2a;margin-top:6px}
.btn-quote{position:absolute;left:230px;top:208px;width:204px;height:60px;background:var(--brand);color:var(--white);font-size:22px;line-height:60px}
.slide-arrow{position:absolute;top:308px;width:62px;height:62px;border:2px solid var(--white);border-radius:50%}
.slide-arrow svg{position:absolute;inset:0;margin:auto}

/* About */
.about{top:569px;height:568px}
.about-photo{left:85px;top:60px;width:465px;height:344px;background:linear-gradient(135deg,#c9b59a,#8b7a68 60%,#4e4a46)}
.about-video{left:237px;top:305px;width:332px;height:191px;background:#2b2b2b}
.about-video svg{position:absolute;left:136px;top:66px}
.about-copy{left:610px;top:70px;width:500px}
.about-copy .label{font-size:31px;font-weight:300}
.about-copy h2{font-size:35px;font-weight:600;color:var(--brand);margin-top:-4px}
.about-copy p{font-size:11.5px;line-height:19px;color:#4a4a4a;margin-top:14px}
.btn-small{display:inline-block;margin-top:18px;background:var(--brand);color:var(--white);font-size:12px;padding:12px 28px;box-shadow:2px 3px 4px rgba(0,0,0,.3)}

/* Quote */
.quote{top:1137px;height:576px;background:linear-gradient(180deg,#2b2824,#1a1a1c);color:var(--white)}
.quote h2{position:absolute;top:58px;width:100%;text-align:center;font-size:36px;font-weight:600}
.quote .sub{position:absolute;top:114px;width:100%;text-align:center;font-size:15px;font-style:italic}
.field{position:absolute;left:102px;width:462px;height:46px;border:1px solid #cfcfcf;font-size:13px;padding:13px 18px;color:#ddd}
.field-msg{position:absolute;left:593px;top:170px;width:465px;height:244px;border:1px solid #cfcfcf;font-size:13px;padding:13px 18px;color:#ddd}
.btn-submit{position:absolute;left:496px;top:467px;width:166px;height:44px;border:1px solid #ddd;border-radius:4px;text-align:center;line-height:42px;font-size:15px}

/* Offer */
.offer{top:1713px;height:477px;text-align:center}
.offer h2{position:absolute;top:42px;width:100%;font-size:36px;font-weight:600;color:var(--brand)}
.offer .intro{position:absolute;top:100px;width:100%;font-size:16px;line-height:27px;color:var(--muted)}
.service{position:absolute;top:179px;width:240px}
.service .icon{width:102px;height:102px;border-radius:50%;background:var(--brand);margin:0 auto;position:relative}
.service .icon svg{position:absolute;inset:0;margin:auto}
.service h3{font-size:15px;font-weight:400;margin-top:22px}
.service p{font-size:10.5px;line-height:19px;color:var(--muted);margin-top:6px}

/* Testimonial */
.testimonial{top:2190px;height:314px;background:linear-gradient(90deg,#1c1c1e,#2a2726,#1c1c1e);color:var(--white)}
.testimonial h2{position:absolute;top:36px;width:100%;text-align:center;font-size:34px;font-weight:500}
.avatar{left:89px;top:131px;width:126px;height:126px;border-radius:50%;border:4px solid var(--white);background:linear-gradient(160deg,#a98a78,#5b4a44)}
.divider{left:254px;top:128px;width:2px;height:130px;background:#bbb}
.quote-text{left:286px;top:130px;width:860px;font-size:13.5px;line-height:26px}
.quote-text .by{font-size:19px;margin-top:10px}
.t-arrow{position:absolute;top:136px}

/* News */
.news{top:2504px;height:642px}
.news h2{position:absolute;top:66px;width:100%;text-align:center;font-size:34px;font-weight:600;color:var(--brand)}
.card{position:absolute;top:139px;width:307px}
.card .thumb{height:184px}
.card h3{font-size:19px;font-weight:500;margin-top:34px;padding-bottom:14px;border-bottom:1px solid #e5e5e5}
.card .meta{display:flex;gap:44px;font-size:11px;color:var(--brand);margin-top:14px;padding-left:20px}
.card .meta span{display:flex;align-items:center;gap:8px}
.card p{font-size:12px;line-height:22px;color:var(--muted);margin-top:22px}
.card .more{font-size:12px;color:#555;margin-top:10px}

/* Subscribe */
.subscribe{top:3146px;height:375px;background:linear-gradient(180deg,#1f1e22,#19191c);color:var(--white);text-align:center}
.subscribe h2{position:absolute;top:72px;width:100%;font-size:36px;font-weight:400}
.sub-input{position:absolute;left:249px;top:148px;width:436px;height:53px;border:1px solid #aaa;text-align:left;padding:15px 34px;font-size:15px;color:#999}
.sub-btn{position:absolute;left:699px;top:148px;width:252px;height:53px;background:#1e6bab;font-size:16px;line-height:53px;letter-spacing:1px}
.sub-social{position:absolute;top:262px;width:48px;height:48px;border:2px solid #8a8a8a;border-radius:50%}

/* Footer */
.site-footer{top:3521px;height:108px;background:var(--footer);color:var(--white);font-size:14px;text-align:center;line-height:108px}
</style>
</head>
<body>

<header class="hero">
  <div class="hero-photo" role="img" aria-label="Upward view of glass office towers against the sky"></div>
  <nav class="nav">
    <div class="brand">Ferncliff Capital</div>
    <ul class="menu">
      <li>HOME</li><li>About Us</li><li>What We Offer</li><li>TEAM &amp; EXPERIENCE</li><li>CONTACTS</li>
    </ul>
    <div class="social-top" aria-label="Social links">
      <span style="background:#3b5a9a"></span><span style="background:#2aa3dc"></span><span style="background:#dc4a38"></span>
    </div>
  </nav>
  <div class="slide-arrow" style="left:22px"><svg width="26" height="26" viewBox="0 0 26 26"><path d="M16 5 L8 13 L16 21 M8 13 H22" fill="none" stroke="#fff" stroke-width="2.5"/></svg></div>
  <div class="slide-arrow" style="right:22px"><svg width="26" height="26" viewBox="0 0 26 26"><path d="M10 5 L18 13 L10 21 M18 13 H4" fill="none" stroke="#fff" stroke-width="2.5"/></svg></div>
  <div class="welcome-panel">
    <div class="kicker">Welcome to</div>
    <div class="name">Ferncliff Capital</div>
    <div class="tag">We are a new commercial real estate company</div>
    <div class="btn-quote">Get a Quote</div>
  </div>
</header>

<section class="about">
  <div class="abs about-photo" role="img" aria-label="Business meeting in a bright office"></div>
  <div class="abs about-video" role="img" aria-label="Company video thumbnail">
    <svg width="60" height="60" viewBox="0 0 60 60"><circle cx="30" cy="30" r="26" fill="none" stroke="#fff" stroke-width="4"/><path d="M24 18 L42 30 L24 42 Z" fill="#fff"/></svg>
  </div>
  <div class="abs about-copy">
    <div class="label">About</div>
    <h2>Ferncliff Capital</h2>
    <p>Lorem Ipsum is simply dummy text of the printing and typesetting industry. Lorem Ipsum has been the industry's standard dummy text ever since the 1500s, when an unknown printer took a galley of type and scrambled it to make a type specimen book. It has survived not only five centuries, but also the leap into electronic typesetting, remaining essentially unchanged.</p>
    <p>It was popularised in the 1960s with the release of Transfix sheets containing Lorem Ipsum passages, and more recently with desktop publishing software like Quillset Composer including versions of Lorem Ipsum. Lorem Ipsum is simply dummy text of the printing and typesetting industry.</p>
    <div class="btn-small">GET A QUOTE</div>
  </div>
</section>

<section class="quote">
  <h2>Get a Quote</h2>
  <div class="sub">"Neque porro quisquam est qui dolorem ipsum quia dolor sit amet, consectetur, adipisci velit..."</div>
  <div class="field" style="top:170px">Full Name:</div>
  <div class="field" style="top:233px">Funding Amount</div>
  <div class="field" style="top:296px">Email Id *</div>
  <div class="field" style="top:359px">Type of Project
    <svg class="abs" style="right:18px;top:18px" width="16" height="10" viewBox="0 0 16 10"><path d="M0 0 H16 L8 10 Z" fill="#fff"/></svg>
  </div>
  <div class="field-msg">Tell Us About Your Project</div>
  <div class="btn-submit">Submit</div>
</section>

<section class="offer">
  <h2>We Offer</h2>
  <div class="intro">Lorem Ipsum is simply dummy text of the printing and typesetting industry.<br>Lorem Ipsum has been the industry's standard dummy text ever since the 1500s.</div>
  <div class="service" style="left:95px">
    <div class="icon"><svg width="34" height="40" viewBox="0 0 34 40"><rect x="5" y="2" width="24" height="36" fill="none" stroke="#fff" stroke-width="3"/><g fill="#fff"><rect x="10" y="8" width="5" height="5"/><rect x="19" y="8" width="5" height="5"/><rect x="10" y="17" width="5" height="5"/><rect x="19" y="17" width="5" height="5"/><rect x="14" y="28" width="6" height="10"/></g></svg></div>
    <h3>HMO Mortgages</h3>
    <p>Simple dummy text of the lending and finance industry. Lorem Ipsum has been the standard dummy text ever since the 1500s.</p>
  </div>
  <div class="service" style="left:352px">
    <div class="icon"><svg width="40" height="40" viewBox="0 0 40 40"><rect x="4" y="12" width="20" height="24" fill="none" stroke="#fff" stroke-width="3"/><rect x="15" y="4" width="20" height="24" fill="var(--brand)" stroke="#fff" stroke-width="3"/></svg></div>
    <h3>Buy-to-let Mortgages</h3>
    <p>Simple dummy text of the lending and finance industry. Lorem Ipsum has been the standard dummy text ever since the 1500s.</p>
  </div>
  <div class="service" style="left:606px">
    <div class="icon"><svg width="44" height="36" viewBox="0 0 44 36"><rect x="7" y="4" width="30" height="21" fill="none" stroke="#fff" stroke-width="3"/><path d="M2 30 H42" stroke="#fff" stroke-width="4"/></svg></div>
    <h3>Online Legal Conveyancing</h3>
    <p>Simple dummy text of the lending and finance industry. Lorem Ipsum has been the standard dummy text ever since the 1500s.</p>
  </div>
  <div class="service" style="left:860px">
    <div class="icon"><svg width="48" height="36" viewBox="0 0 48 36" fill="#fff"><circle cx="24" cy="9" r="7"/><path d="M12 32 Q12 18 24 18 Q36 18 36 32 Z"/><circle cx="10" cy="13" r="5"/><path d="M1 30 Q1 20 10 20 Q14 20 15 22 Q11 26 11 30 Z"/><circle cx="38" cy="13" r="5"/><path d="M47 30 Q47 20 38 20 Q34 20 33 22 Q37 26 37 30 Z"/></svg></div>
    <h3>Joint Venture Funding</h3>
    <p>Simple dummy text of the lending and finance industry. Lorem Ipsum has been the standard dummy text ever since the 1500s.</p>
  </div>
</section>

<section class="testimonial">
  <h2>What People say About us</h2>
  <svg class="t-arrow" style="left:10px" width="20" height="34" viewBox="0 0 20 34"><path d="M16 3 L4 17 L16 31" fill="none" stroke="#ccc" stroke-width="3"/></svg>
  <svg class="t-arrow" style="right:10px" width="20" height="34" viewBox="0 0 20 34"><path d="M4 3 L16 17 L4 31" fill="none" stroke="#ccc" stroke-width="3"/></svg>
  <div class="abs avatar" role="img" aria-label="Client portrait"></div>
  <div class="abs divider"></div>
  <div class="abs quote-text">
    Lorem Ipsum is simply dummy text of the printing and typesetting industry. Lorem Ipsum has been the industry's standard dummy text ever since the 1500s, when an unknown printer took a galley of type and scrambled it to make a type specimen book. It has survived not only five centuries, but also the leap into elunchanged.
    <div class="by">- Marisol T. Averill.</div>
  </div>
</section>

<section class="news">
  <h2>Latest News</h2>
  <article class="card" style="left:85px">
    <div class="thumb" role="img" aria-label="Executive standing outside an office building" style="background:linear-gradient(160deg,#c8d3dc,#6f7d8c 60%,#3d4654)"></div>
    <h3>Lorem Ipsum is simply dummy</h3>
    <div class="meta"><span><svg width="14" height="14" viewBox="0 0 14 14"><rect x="1" y="2" width="12" height="11" fill="none" stroke="#e29a3a" stroke-width="1.5"/><path d="M1 5 H13" stroke="#e29a3a" stroke-width="1.5"/></svg>Sep 26, 2017</span><span><svg width="16" height="13" viewBox="0 0 16 13"><path d="M1 1 H15 V9 H6 L2 12 V9 H1 Z" fill="#e29a3a"/></svg>Comments</span></div>
    <p>No sit consul invidunt platonem, te vel laoreet meliore, viris scaevola consequat vis ad. Cu paulo partiendo quanim nonumes ..</p>
    <div class="more">Read More ›</div>
  </article>
  <article class="card" style="left:447px">
    <div class="thumb" role="img" aria-label="Businessman facing a drawn skyline chart" style="background:linear-gradient(180deg,#d8dadc,#a7aaae 70%,#6c6f73)"></div>
    <h3>Lorem Ipsum is simply dummy</h3>
    <div class="meta"><span><svg width="14" height="14" viewBox="0 0 14 14"><rect x="1" y="2" width="12" height="11" fill="none" stroke="#e29a3a" stroke-width="1.5"/><path d="M1 5 H13" stroke="#e29a3a" stroke-width="1.5"/></svg>Sep 26, 2017</span><span><svg width="16" height="13" viewBox="0 0 16 13"><path d="M1 1 H15 V9 H6 L2 12 V9 H1 Z" fill="#e29a3a"/></svg>Comments</span></div>
    <p>No sit consul invidunt platonem, te vel laoreet meliore, viris scaevola consequat vis ad. Cu paulo partiendo quanim nonumes ..</p>
    <div class="more">Read More ›</div>
  </article>
  <article class="card" style="left:806px">
    <div class="thumb" role="img" aria-label="Two colleagues talking by an office window" style="background:linear-gradient(90deg,#e6edf2,#b8c6d2 50%,#7f8e9c)"></div>
    <h3>Lorem Ipsum is simply dummy</h3>
    <div class="meta"><span><svg width="14" height="14" viewBox="0 0 14 14"><rect x="1" y="2" width="12" height="11" fill="none" stroke="#e29a3a" stroke-width="1.5"/><path d="M1 5 H13" stroke="#e29a3a" stroke-width="1.5"/></svg>Sep 26, 2017</span><span><svg width="16" height="13" viewBox="0 0 16 13"><path d="M1 1 H15 V9 H6 L2 12 V9 H1 Z" fill="#e29a3a"/></svg>Comments</span></div>
    <p>No sit consul invidunt platonem, te vel laoreet meliore, viris scaevola consequat vis ad. Cu paulo partiendo quanim nonumes ..</p>
    <div class="more">Read More ›</div>
  </article>
</section>

<section class="subscribe">
  <h2>Subscribe Now!</h2>
  <div class="sub-input">Enter your email.</div>
  <div class="sub-btn">GET STARTED</div>
  <div class="sub-social" style="left:460px"></div>
  <div class="sub-social" style="left:537px"></div>
  <div class="sub-social" style="left:617px"></div>
  <div class="sub-social" style="left:695px"></div>
</section>

<footer class="site-footer">Copyright (c) 2017. Ferncliff Capital. All rights reserved.</footer>

</body>
</html>
```